Podiatry clinic requires a modern revamp and editing of existing website.

I would like a fresh new look and updated information for my current business website. An easy to navigate site with prominent address and phone number for call to action. We are a podiatry clinic that focuses on general and sports podiatry.
I would like 4 pages; including Home page, About Us, Services & Contact.
www.brambleridgepodiatry.net

Target Market(s)

Active working professionals.

Industry/Entity Type

Medical

Coding

Coded - Design and coding required

Number of Pages Required

4 page

Font styles to use
Sans Serif

Colors
6b449b

Requirements
Must have
• A modern look with logo and active images; clean and uncluttered. Visible phone number and address for call to action.
• 4 pages - Home, About Us, Services, Contact.
• Home page - update address & service logos.
• About Us - update of personal information.
• Services - Revamp of existing page.
• Contact page to include Google map, email & phone number.
Nice to have
• Ability to add content easily; eg. a blog or adding video onto Home page.
• Link to Facebook page.

```html
<!DOCTYPE html>
<html lang="en">
<head>
<meta charset="utf-8">
<title>Bramble Ridge Podiatry</title>
<link href="https://fonts.googleapis.com/css2?family=Raleway:wght@400;500;600;700&family=Lato:wght@400;700&display=swap" rel="stylesheet">
<style>
:root{
  --orange:#ef6f22;
  --green:#7cbf3a;
  --purple:#4a3a96;
  --ink:#111111;
  --text:#333333;
  --grey-bg:#f5f5f5;
  --rule:#bdbdbd;
  --white:#ffffff;
  --footer:#1c2431;
}
*{box-sizing:border-box;margin:0;padding:0}
html,body{width:1200px;height:2236px;overflow:hidden}
body{font-family:'Lato',sans-serif;color:var(--text);background:var(--white);position:relative}
a{color:inherit;text-decoration:none}

/* header */
.site-header{position:absolute;top:0;left:0;width:1200px;height:128px;background:var(--white);box-shadow:0 2px 4px rgba(0,0,0,.25);z-index:2}
.brand{position:absolute;left:100px;top:22px;display:flex;align-items:center;gap:10px;font-family:'Raleway',sans-serif;font-weight:700;font-size:25px;color:var(--purple);line-height:1.05;width:200px}
.brand-dot{width:22px;height:22px;border-radius:50%;background:var(--purple);flex:none}
.header-contacts{position:absolute;right:96px;top:28px;display:flex;gap:24px;font-family:'Raleway',sans-serif;font-weight:700;font-size:14px;color:var(--ink)}
.header-contacts span{display:flex;align-items:center;gap:8px}
.icon-dot{width:28px;height:28px;border-radius:50%;background:var(--green);display:flex;align-items:center;justify-content:center}
.main-nav{position:absolute;left:450px;top:96px;display:flex;gap:44px;font-family:'Raleway',sans-serif;font-weight:600;font-size:16px;color:var(--ink)}
.main-nav .current{color:var(--purple)}
.btn-book{position:absolute;left:882px;top:86px;width:219px;height:33px;background:var(--orange);color:var(--white);font-family:'Raleway',sans-serif;font-weight:600;font-size:14px;display:flex;align-items:center;justify-content:center;gap:10px}

/* hero */
.hero{position:absolute;top:128px;left:0;width:1200px;height:470px;background:linear-gradient(100deg,#d9d6d2 0%,#c8453f 28%,#e8e6e3 48%,#f4f4f4 70%,#dcdcdc 100%)}
.hero-arrow{position:absolute;top:182px}
.hero-caption{position:absolute;left:0;bottom:0;width:100%;height:56px;background:rgba(40,40,40,.72);color:var(--white);font-family:'Raleway',sans-serif;font-weight:600;font-size:29px;display:flex;align-items:center;justify-content:center}

/* section titles */
.section-title{font-family:'Raleway',sans-serif;font-weight:700;font-size:32px;color:var(--ink);text-align:center}
.section-title .o{color:var(--orange)}
.section-title .g{color:var(--green)}
.title-rule{width:576px;height:1px;background:var(--rule);margin:14px auto 0;position:relative}
.title-rule::after{content:"";position:absolute;left:50%;top:-1px;width:32px;height:3px;margin-left:-16px;background:var(--orange)}

/* welcome */
.welcome{position:absolute;top:598px;left:0;width:1200px;height:327px;padding-top:42px}
.welcome p{width:1040px;margin:34px auto 0;text-align:center;font-size:14px;line-height:26.5px;color:var(--text)}
.btn-small{display:block;width:110px;height:33px;margin:30px auto 0;background:var(--orange);color:var(--white);border-radius:3px;font-family:'Raleway',sans-serif;font-size:12px;font-weight:600;line-height:33px;text-align:center}

/* treatments */
.treatments{position:absolute;top:925px;left:0;width:1200px;height:568px;background:var(--grey-bg);padding-top:30px}
.treatments .intro{width:1000px;margin:28px auto 0;text-align:center;font-size:16px;line-height:27px;color:var(--ink)}
.card-row{position:absolute;top:205px;left:99px;display:flex;gap:26px}
.card{width:231px;height:273px;background:var(--white);position:relative;text-align:center;border-bottom:3px solid var(--green)}
.card.alt{border-bottom-color:var(--orange)}
.card-icon{width:76px;height:76px;border-radius:50%;background:var(--green);margin:45px auto 0}
.card.alt .card-icon{background:var(--orange)}
.card h3{font-family:'Raleway',sans-serif;font-weight:600;font-size:16px;color:var(--ink);margin-top:30px}
.card p{font-size:13px;line-height:22px;color:var(--ink);margin-top:8px;padding:0 12px}
.card-plus{position:absolute;left:50%;bottom:0;width:46px;height:23px;margin-left:-23px;border-radius:23px 23px 0 0;background:var(--green);color:var(--white);font-size:20px;line-height:26px}
.card.alt .card-plus{background:var(--orange)}
.carousel-arrow{position:absolute;top:330px}

/* inquiry */
.inquiry{position:absolute;top:1493px;left:0;width:1200px;height:280px;background:var(--orange);color:var(--white)}
.inquiry h2{position:absolute;left:100px;top:72px;font-family:'Raleway',sans-serif;font-weight:700;font-size:35px}
.inquiry .blurb{position:absolute;left:100px;top:136px;width:300px;font-size:12.5px;line-height:22px}
.form-label{position:absolute;left:459px;top:47px;font-family:'Raleway',sans-serif;font-weight:700;font-size:15px}
.field{position:absolute;width:309px;height:42px;background:var(--white);color:#666;font-size:12px;padding:0 13px;line-height:42px}
.btn-submit{position:absolute;left:459px;top:186px;width:163px;height:43px;background:var(--ink);color:var(--white);font-family:'Raleway',sans-serif;font-weight:700;font-size:16px;display:flex;align-items:center;justify-content:center}

/* footer */
.site-footer{position:absolute;top:1773px;left:0;width:1200px;height:463px;border-top:3px solid #2c5d9b;background:linear-gradient(180deg,#1b2433 0%,#222b38 45%,#2d2a28 80%,#151a22 100%);color:var(--white)}
.footer-contacts{position:absolute;top:40px;left:0;width:100%}
.footer-item{position:absolute;width:380px;text-align:center;font-size:14px;font-weight:700}
.footer-item svg{display:block;margin:0 auto 14px}
.footer-brand{position:absolute;left:0;top:160px;width:100%;display:flex;justify-content:center;align-items:center;gap:12px;font-family:'Raleway',sans-serif;font-weight:700;font-size:34px;color:var(--white)}
.footer-brand .brand-dot{background:var(--white);width:28px;height:28px}
.footer-nav{position:absolute;top:340px;left:0;width:100%;display:flex;justify-content:center;gap:22px;font-size:14px}
.footer-nav a+a::before{content:"•";margin-right:12px;color:#999}
.footer-bottom{position:absolute;top:392px;left:100px;width:1000px;border-top:1px solid rgba(255,255,255,.15);padding-top:30px;font-size:13px}
.social{position:absolute;right:0;top:18px;display:flex;gap:12px}
.social span{width:34px;height:34px;border-radius:50%;border:2px solid var(--white)}
</style>
</head>
<body>

<header class="site-header">
  <div class="brand"><span class="brand-dot"></span>Bramble Ridge Podiatry</div>
  <div class="header-contacts">
    <span><span class="icon-dot"><svg width="14" height="10" viewBox="0 0 14 10"><rect x="0.5" y="0.5" width="13" height="9" fill="none" stroke="#fff"/><path d="M0.5 0.5 7 6 13.5 0.5" fill="none" stroke="#fff"/></svg></span>info@brambleridgepodiatry.net</span>
    <span><span class="icon-dot"><svg width="14" height="14" viewBox="0 0 24 24"><path d="M6.6 10.8a15 15 0 0 0 6.6 6.6l2.2-2.2c.3-.3.7-.4 1-.2 1.1.4 2.3.6 3.6.6.6 0 1 .4 1 1V20c0 .6-.4 1-1 1A17 17 0 0 1 3 4c0-.6.4-1 1-1h3.5c.6 0 1 .4 1 1 0 1.3.2 2.5.6 3.6.1.3 0 .7-.2 1z" fill="#fff"/></svg></span>(310) 555-0148</span>
  </div>
  <nav class="main-nav">
    <a class="current" href="#">home</a>
    <a href="#">about us</a>
    <a href="#">services</a>
    <a href="#">contact us</a>
  </nav>
  <a class="btn-book" href="#"><svg width="18" height="18" viewBox="0 0 18 18"><rect x="1" y="3" width="13" height="13" fill="none" stroke="#fff" stroke-width="1.5"/><circle cx="13" cy="13" r="4" fill="var(--orange)" stroke="#fff" stroke-width="1.5"/></svg>book an appointment</a>
</header>

<section class="hero" role="img" aria-label="Photo of a physiotherapist supporting a patient's arm during a shoulder exercise">
  <svg class="hero-arrow" style="left:44px" width="36" height="64" viewBox="0 0 36 64"><path d="M32 2 4 32l28 30" fill="none" stroke="#fff" stroke-width="2"/></svg>
  <svg class="hero-arrow" style="right:44px" width="36" height="64" viewBox="0 0 36 64"><path d="M4 2l28 30L4 62" fill="none" stroke="#fff" stroke-width="2"/></svg>
  <div class="hero-caption">Bramble Ridge Podiatry is a Podiatry clinic in the heart of Melbourne</div>
</section>

<section class="welcome">
  <h1 class="section-title">welcome to <span class="o">bramble ridge</span> <span class="g">podiatry</span></h1>
  <div class="title-rule"></div>
  <p>Lorem ipsum dolor sit amet, consectetuer adipiscing elit, sed diam nonummy nibh euismod tincidunt ut laoreet dolore magna aliquam erat volutpat. Ut wisi enim ad minim veniam, quis nostrud exerci tation ullamcorper suscipit lobortis nisl ut aliquip ex ea commodo consequat. Duis autem vel eum iriure dolor in hendrerit in vulputate velit esse molestie consequat, vel illum dolore eu feugiat nulla facilisis at vero eros et accumsan et iusto odio dignissim qui blandit praesent luptatum zzril delenit augue duis dolore te feugait nulla facilisi.</p>
  <a class="btn-small" href="#">read more</a>
</section>

<section class="treatments">
  <h2 class="section-title">podiatry <span class="o">treatments</span></h2>
  <div class="title-rule"></div>
  <p class="intro">Lorem ipsum dolor sit amet, consectetuer adipiscing elit, sed diam nonummy nibh euismod tincidunt ut laoreet dolore magna aliquam erat volutpat. Ut wisi enim ad minim veniam, quis nostrud exerci tation ullamcorper suscipit lobortis nisl ut</p>
  <svg class="carousel-arrow" style="left:50px" width="14" height="24" viewBox="0 0 14 24"><path d="M12 2 2 12l10 10" fill="none" stroke="#8a8fb5" stroke-width="2"/></svg>
  <svg class="carousel-arrow" style="right:50px" width="14" height="24" viewBox="0 0 14 24"><path d="M2 2l10 10L2 22" fill="none" stroke="#8a8fb5" stroke-width="2"/></svg>
  <div class="card-row">
    <article class="card"><div class="card-icon"></div><h3>treadmill analysis</h3><p>Duis autem vel eum iriure dolor in hendrerit in vulputate</p><span class="card-plus">+</span></article>
    <article class="card alt"><div class="card-icon"></div><h3>orthotis therapy</h3><p>Duis autem vel eum iriure dolor in hendrerit in vulputate</p><span class="card-plus">+</span></article>
    <article class="card"><div class="card-icon"></div><h3>callus</h3><p>Duis autem vel eum iriure dolor in hendrerit in vulputate</p><span class="card-plus">+</span></article>
    <article class="card alt"><div class="card-icon"></div><h3>heel pain</h3><p>Duis autem vel eum iriure dolor in hendrerit in vulputate</p><span class="card-plus">+</span></article>
  </div>
</section>

<section class="inquiry">
  <h2>quick inquiry</h2>
  <p class="blurb">Duis autem vel eum iriure dolormi opl inmokl hendi rerit in vulpu tateml velitm essemol mo molestiel conseqb uat, velmi illum dolor eokf no atn nulla more facilisis... [+]</p>
  <div class="form-label">please fill up bellow form</div>
  <div class="field" style="left:459px;top:83px">name</div>
  <div class="field" style="left:792px;top:83px">email</div>
  <div class="field" style="left:459px;top:135px">phone</div>
  <div class="field" style="left:792px;top:135px">message</div>
  <a class="btn-submit" href="#">submit</a>
</section>

<footer class="site-footer" role="img" aria-label="Night skyline of the city behind the footer">
  <div class="footer-contacts">
    <div class="footer-item" style="left:120px">
      <svg width="330" height="22" viewBox="0 0 330 22"><line x1="55" y1="11" x2="150" y2="11" stroke="#7cbf3a"/><line x1="180" y1="11" x2="275" y2="11" stroke="#7cbf3a"/><path d="M165 20c-5-6-7-9-7-12a7 7 0 0 1 14 0c0 3-2 6-7 12z" fill="none" stroke="#fff" stroke-width="1.4"/><circle cx="165" cy="8" r="2.5" fill="none" stroke="#fff" stroke-width="1.4"/></svg>
      Suite 12/88 Larkspur Street Melbourne 3000</div>
    <div class="footer-item" style="left:410px">
      <svg width="330" height="22" viewBox="0 0 330 22"><line x1="55" y1="11" x2="150" y2="11" stroke="#7cbf3a"/><line x1="180" y1="11" x2="275" y2="11" stroke="#7cbf3a"/><path d="M159 3c2 0 3 3 4 5l-2 2a10 10 0 0 0 5 5l2-2c2 1 5 2 5 4s-2 3-3 3c-6 0-13-7-13-13 0-2 1-4 2-4z" fill="none" stroke="#fff" stroke-width="1.4"/></svg>
      Phone: 1300 482 907</div>
    <div class="footer-item" style="left:700px">
      <svg width="330" height="22" viewBox="0 0 330 22"><line x1="55" y1="11" x2="150" y2="11" stroke="#7cbf3a"/><line x1="180" y1="11" x2="275" y2="11" stroke="#7cbf3a"/><path d="M155 11 175 3l-5 17-5-7z M165 13l10-10" fill="none" stroke="#fff" stroke-width="1.4"/></svg>
      Email: info@brambleridgepodiatry.net</div>
  </div>
  <div class="footer-brand"><span class="brand-dot"></span>Bramble Ridge Podiatry</div>
  <nav class="footer-nav">
    <a href="#">home</a><a href="#">about us</a><a href="#">services</a><a href="#">contact us</a>
  </nav>
  <div class="footer-bottom">
    Copyright © 2016 Bramble Ridge Podiatry.&nbsp; All Right Reserved.
    <div class="social"><span></span><span></span><span></span><span></span></div>
  </div>
</footer>

</body>
</html>
```